LM-Steuerberatung WordPress Site fully implemented (tax advisor)

Hello!
I need a little Wordpress Site for my newly founded Tax-Advisor Company.
I am a one-man Office advising in the area of Crypto-Currency.
PLEASE only provide a Design, if you can also Implement a WP-Site afterwards on an existing Webspace.

Please find the Content and Website-Description in the attached Document

Language for the Website is German (for now)

Target Market(s)

Tax-Advisory (specialized in Crypto Currency)

Coding

Coded - Design and coding required

Number of Pages Required

5+ page

Font styles to use
Sans Serif

Requirements
Must have
• Wordpress Implementation afterwards - Details according to attached Project Information Document

```html
<!DOCTYPE html>
<html lang="de">
<head>
<meta charset="utf-8">
<title>LM-Steuerberatung</title>
<link href="https://fonts.googleapis.com/css2?family=Montserrat:wght@500;700;800&family=Mulish:wght@400;500&display=swap" rel="stylesheet">
<style>
  :root {
    --navy: #1b2a42;
    --grey: #a6a6a6;
    --white: #ffffff;
    --text: #1d2230;
    --rule: #3a4860;
  }
  * { margin: 0; padding: 0; box-sizing: border-box; }
  html, body { width: 1200px; height: 880px; overflow: hidden; background: var(--white); }
  body { position: relative; font-family: "Mulish", Arial, sans-serif; color: var(--navy); }

  .site-header { position: absolute; top: 0; left: 0; width: 1200px; height: 80px; }
  .brand { position: absolute; top: 26px; left: 130px; display: flex; align-items: center; gap: 10px; }
  .brand-mark { width: 30px; height: 30px; background: var(--navy); }
  .brand-name { font-family: "Montserrat", Arial, sans-serif; font-weight: 700; font-size: 16px; letter-spacing: 0.2px; color: var(--navy); }
  .main-nav { position: absolute; top: 30px; right: 133px; display: flex; gap: 42px; }
  .main-nav a { font-family: "Montserrat", Arial, sans-serif; font-weight: 500; font-size: 13.5px; color: var(--navy); text-decoration: none; line-height: 16px; padding: 2px 0; }
  .main-nav a.active { border-top: 1.5px solid var(--navy); border-bottom: 1.5px solid var(--navy); }

  .hero-visual { position: absolute; top: 140px; left: 0; width: 1200px; height: 577px;
    background: linear-gradient(180deg, #ffffff 0%, #f7f7f7 40%, #e9e9e9 70%, #f4f4f4 100%); }

  .hero { position: absolute; top: 92px; left: 0; width: 1200px; text-align: center; }
  .hero-title { font-family: "Montserrat", Arial, sans-serif; font-weight: 800; font-size: 27px; color: var(--navy); letter-spacing: -0.2px; }
  .hero-title .soft { color: var(--grey); }
  .hero-lead { margin-top: 18px; font-size: 18px; line-height: 27px; color: var(--text); }
  .hero-button { display: inline-flex; align-items: center; gap: 14px; margin-top: 22px; height: 48px; padding: 0 18px;
    background: var(--navy); color: var(--white); font-family: "Montserrat", Arial, sans-serif; font-weight: 800; font-size: 15.5px; text-decoration: none; }

  .quote { position: absolute; top: 507px; left: 355px; width: 503px; height: 98px; background: rgba(255,255,255,0.75);
    display: flex; align-items: center; justify-content: center; text-align: center; font-size: 18px; line-height: 30px; color: var(--text); }

  .site-footer { position: absolute; top: 717px; left: 0; width: 1200px; height: 163px; background: var(--navy); color: var(--white); }
  .site-footer .brand { top: 46px; left: 131px; }
  .site-footer .brand-mark { background: var(--white); }
  .site-footer .brand-name { color: var(--white); }
  .contact { position: absolute; top: 33px; right: 133px; text-align: right; font-size: 16px; line-height: 29px; }
  .footer-rule { position: absolute; top: 124px; left: 132px; width: 663px; height: 1px; background: var(--rule); }
  .legal { position: absolute; top: 115px; right: 133px; font-size: 11px; }
  .legal span { margin: 0 9px; }
</style>
</head>
<body>
  <header class="site-header">
    <div class="brand"><span class="brand-mark"></span><span class="brand-name">LM STEUERBERATUNG</span></div>
    <nav class="main-nav">
      <a class="active" href="#">HOME</a>
      <a href="#">LEISTUNGEN</a>
      <a href="#">ÜBER MICH</a>
      <a href="#">KONTAKT</a>
    </nav>
  </header>

  <div class="hero-visual" role="img" aria-label="Perspektivisches Gitter mit leuchtenden Datenpunkten in Grautönen"></div>

  <section class="hero">
    <h1 class="hero-title"><span class="soft">WILLKOMMEN</span> BEI LM-STEUERBERATUNG!</h1>
    <p class="hero-lead">Ihrem Spezialisten bei allen steuerlichen Themen rund<br>um Einkünfte &amp; Vermögen aus Krypto-Assets.</p>
    <a class="hero-button" href="#">CONTINUE TO OUR SERVICES
      <svg width="12" height="18" viewBox="0 0 12 18" aria-hidden="true"><path d="M2 2l7 7-7 7" fill="none" stroke="#fff" stroke-width="2"/></svg>
    </a>
  </section>

  <blockquote class="quote">Dann mach ich eine Schweizer Holding-Gesellschaft–<br>dort zahlt man fast keine Steuern</blockquote>

  <footer class="site-footer">
    <div class="brand"><span class="brand-mark"></span><span class="brand-name">LM STEUERBERATUNG</span></div>
    <div class="contact">Email: office@lm-steuer-beratung.at<br>Phone : +43 512 480 276</div>
    <div class="footer-rule"></div>
    <div class="legal">Imprint<span>|</span>Copyright © 2022 All Rights Reserved</div>
  </footer>
</body>
</html>
```